Harborline Auto LLC

Car Dealer Customer Service
Address: 2874 Cresthaven Road, Shelbyville, TN 37162
web: www.harborlineautoxq.net
email: harborlineautoxq@mailnest.example
Phone: (931) 555-0148
Phone: (629) 555-0173

```html
<!DOCTYPE html>
<html lang="en">
<head>
<meta charset="utf-8">
<title>Harborline Auto LLC – Business Card</title>
<link href="https://fonts.googleapis.com/css2?family=Montserrat:wght@400;500;800&display=swap" rel="stylesheet">
<style>
  :root {
    --brand-blue: #1d7bad;
    --accent-gold: #ecb445;
    --paper: #ffffff;
    --backdrop: #8d8d8d;
    --text-light: #ffffff;
  }
  * { margin: 0; padding: 0; box-sizing: border-box; }
  html, body {
    width: 1160px; height: 1200px; overflow: hidden;
    background: var(--backdrop);
    font-family: "Montserrat", sans-serif;
  }
  .card {
    position: absolute; left: 199px; width: 777px; height: 441px;
    overflow: hidden;
  }
  .card--front { top: 105px; background: var(--paper); }
  .card--back { top: 634px; height: 444px; background: var(--brand-blue); }

  .front-shape { position: absolute; inset: 0; width: 100%; height: 100%; }

  .contact-block {
    position: absolute; left: 26px; top: 112px;
    color: var(--text-light); font-size: 18px; font-weight: 400; line-height: 29px;
  }
  .contact-list { list-style: none; margin-top: 16px; }
  .contact-list li { display: flex; align-items: center; height: 31px; }
  .contact-icon { width: 17px; height: 17px; margin-left: 1px; margin-right: 13px; flex: none; }

  .wordmark {
    position: absolute; font-weight: 800; letter-spacing: 0.5px; white-space: nowrap;
    transform: translateX(-50%);
  }
  .wordmark--front { left: 615px; top: 256px; font-size: 25px; color: var(--brand-blue); }
  .wordmark--back { left: 50%; top: 310px; font-size: 46px; color: var(--text-light); }

  .mark-dot {
    position: absolute; border-radius: 50%; background: var(--accent-gold);
  }
  .mark-dot--front { left: 570px; top: 132px; width: 90px; height: 90px; }
  .mark-dot--back { left: 298px; top: 95px; width: 180px; height: 180px; }
</style>
</head>
<body>
  <section class="card card--front">
    <svg class="front-shape" viewBox="0 0 777 441" preserveAspectRatio="none" aria-hidden="true">
      <rect width="777" height="441" fill="var(--brand-blue)"/>
      <path d="M495 0 Q341.5 220.5 474 441 L777 441 L777 0 Z" fill="var(--accent-gold)"/>
      <path d="M495 0 Q365 220.5 511 441 L777 441 L777 0 Z" fill="var(--paper)"/>
    </svg>

    <div class="contact-block">
      <p class="contact-role">Car Dealer Customer Service</p>
      <p class="contact-address">2874 Cresthaven Road<br>Shelbyville, TN 37162</p>
      <ul class="contact-list">
        <li>
          <svg class="contact-icon" viewBox="0 0 24 24" aria-hidden="true"><path fill="#fff" d="M6.6 10.8a15 15 0 0 0 6.6 6.6l2.2-2.2a1 1 0 0 1 1-.25 11.4 11.4 0 0 0 3.6.57 1 1 0 0 1 1 1V20a1 1 0 0 1-1 1A17 17 0 0 1 3 4a1 1 0 0 1 1-1h3.5a1 1 0 0 1 1 1c0 1.25.2 2.45.57 3.57a1 1 0 0 1-.25 1z"/></svg>
          (931) 555-0148
        </li>
        <li>
          <svg class="contact-icon" viewBox="0 0 24 24" aria-hidden="true"><path fill="#fff" d="M2 8c3-4 17-4 20 0v2h-5V8H7v2H2z M6 12h12l2 8H4z"/><circle cx="12" cy="16" r="2" fill="var(--brand-blue)"/></svg>
          (629) 555-0173
        </li>
        <li>
          <svg class="contact-icon" viewBox="0 0 24 24" aria-hidden="true"><path fill="#fff" d="M2 5h20v14H2z"/><path d="M2 5l10 8 10-8" fill="none" stroke="var(--brand-blue)" stroke-width="1.8"/></svg>
          harborlineautoxq@mailnest.example
        </li>
        <li>
          <svg class="contact-icon" viewBox="0 0 24 24" aria-hidden="true"><circle cx="12" cy="12" r="10" fill="#fff"/><path d="M7 6c2 1 3 3 2 5s1 3 0 5M15 5c-1 2 1 3 3 3M14 14c2 0 3 2 2 4" fill="none" stroke="var(--brand-blue)" stroke-width="1.6"/></svg>
          www.harborlineautoxq.net
        </li>
      </ul>
    </div>

    <span class="mark-dot mark-dot--front" aria-hidden="true"></span>
    <p class="wordmark wordmark--front">HARBORLINE AUTO</p>
  </section>

  <section class="card card--back">
    <span class="mark-dot mark-dot--back" aria-hidden="true"></span>
    <p class="wordmark wordmark--back">HARBORLINE AUTO</p>
  </section>
</body>
</html>
```